Web app for social movements needs a new look

We are building a Velmora Quill extension called "Pelbo" that helps social movement leaders and advocacy organizations connect with an audience that cares about their cause, and we need to create a more polished website to explain the extension to prospective users. The extension analyzes articles users are reading online and recommends ways they can take action in their local area on the social and political issues they are reading about. For example, if a user is reading about the climate crisis, the extension might display a banner recommending a rally being held by the Kestrel Movement or an opportunity to canvass or phone bank for a pro-Tallow Harbor Pact political candidate. Organizers with progressive organizations can register for an account on our web portal to start posting actions or events that will then be recommended to users through the browser extension if they are reading a relevant article.

We are planning for an upcoming "soft launch" and would like to create a more polished version of our website. The design should include:
– A user-facing page that that concisely explains how the Quill extension works and links to the Quill web store where users can download Pelbo.
– An organizer-facing page that outlines the steps involved for organizers to recommend their organization or a specific action to users through Pelbo: register for an account, post an action or event, your action or event is recommended to users.
– An HTML/CSS template for the organizer portal that we can then take and populate with Django forms or other Django content. This template should include a top menu bar. We've provided an example of the extremely barebones template used in our prototype as an example (base.html).
– A redesigned or improved logo, including one version designed to be put on a white background and one version designed to go on a background of a darker color (e.g., orange). Our current logo is provided. Feel free to use this as a starting point or design something completely different.

The design should convey themes of solidarity, bringing people together to effect positive change, and hope for a better future. We expect that organizations and users on the platform will be focused on a range of progressive issues, including racial justice, immigration justice, gender equity, LGBTQ+ rights, workers' rights, and addressing the climate crisis and economic inequality.

Currently, the color scheme of our prototype browser extension is centered around the color orange, but we are open to designers' ideas about other possible color schemes.

```html
<!DOCTYPE html>
<html lang="en">
<head>
<meta charset="utf-8">
<title>Pelbo — Racial Justice</title>
<link href="https://fonts.googleapis.com/css2?family=Montserrat:wght@600;700;800&family=Nunito:wght@400;600&family=Quicksand:wght@400;500&display=swap" rel="stylesheet">
<style>
  :root {
    --orange: #e8643a;
    --orange-mid: #f07d5a;
    --orange-soft: #eba595;
    --ink: #1b1b1b;
    --text: #2e2e2e;
    --grey-bg: #f5f4f4;
    --footer: #222222;
    --white: #ffffff;
    --rule: #6b6b6b;
  }
  * { margin: 0; padding: 0; box-sizing: border-box; }
  html, body { width: 970px; height: 1200px; overflow: hidden; }
  body { position: relative; background: var(--white); font-family: "Nunito", sans-serif; color: var(--text); }

  .hero {
    position: absolute; left: 0; top: 0; width: 970px; height: 370px;
    background: linear-gradient(160deg, #3a3531 0%, #2a2624 40%, #4a3a30 70%, #2c2a28 100%);
  }
  .hero-photo { position: absolute; inset: 0; background: radial-gradient(ellipse at 30% 40%, rgba(120,90,70,.35), transparent 60%), radial-gradient(ellipse at 80% 60%, rgba(90,80,70,.3), transparent 55%); }
  .brand { position: absolute; display: flex; align-items: center; gap: 9px; }
  .brand-dot { width: 16px; height: 16px; border-radius: 50%; background: var(--orange); }
  .brand-name { font-family: "Montserrat", sans-serif; font-weight: 600; font-size: 17px; color: var(--orange); }
  .site-header .brand { left: 107px; top: 29px; }
  .nav { position: absolute; top: 26px; right: 106px; display: flex; align-items: center; height: 26px; }
  .nav a { color: var(--white); text-decoration: none; font-size: 11px; margin-left: 25px; }
  .nav a:first-child { margin-left: 0; }
  .nav .login { background: var(--orange); font-weight: 700; padding: 0 10px; height: 26px; line-height: 26px; margin-left: 19px; }
  .hero-title { position: absolute; top: 126px; width: 100%; text-align: center; font-family: "Montserrat", sans-serif; font-weight: 800; font-size: 23px; color: var(--white); }
  .hero-text { position: absolute; top: 172px; left: 285px; width: 400px; text-align: center; font-size: 13px; line-height: 21px; color: var(--white); }
  .store-btn { position: absolute; left: 402px; top: 236px; width: 168px; height: 37px; background: var(--orange); color: var(--white); text-decoration: none; font-family: "Montserrat", sans-serif; font-weight: 700; font-size: 12.5px; display: flex; align-items: center; justify-content: center; }

  .steps { position: absolute; left: 0; top: 370px; width: 970px; height: 427px; }
  .section-title { font-family: "Montserrat", sans-serif; font-weight: 800; color: var(--ink); font-size: 15.5px; letter-spacing: .2px; }
  .steps .section-title { position: absolute; top: 33px; width: 100%; text-align: center; }
  .steps svg { position: absolute; left: 0; top: 0; }
  .step { position: absolute; width: 160px; text-align: center; top: 218px; }
  .step h3 { font-family: "Montserrat", sans-serif; font-weight: 700; font-size: 10px; color: var(--ink); margin-bottom: 10px; }
  .step p { font-family: "Quicksand", sans-serif; font-size: 8.5px; line-height: 11.6px; color: var(--ink); }

  .overview { position: absolute; left: 0; top: 797px; width: 970px; height: 320px; background: var(--grey-bg); }
  .overview-art { position: absolute; left: 126px; top: 47px; width: 207px; height: 216px; border-radius: 50%; background: radial-gradient(circle, rgba(232,100,58,.08) 40%, rgba(232,100,58,.22) 100%); }
  .overview-divider { position: absolute; left: 409px; top: 44px; width: 1px; height: 229px; background: #d6d4d4; }
  .overview .section-title { position: absolute; left: 491px; top: 40px; }
  .overview-rule { position: absolute; left: 491px; top: 69px; width: 84px; height: 2px; background: var(--rule); }
  .overview-body { position: absolute; left: 491px; top: 92px; width: 371px; font-size: 11px; line-height: 18.1px; color: var(--text); text-align: justify; }
  .overview-body p + p { margin-top: 18px; }

  .site-footer { position: absolute; left: 0; top: 1117px; width: 970px; height: 83px; background: var(--footer); }
  .site-footer .brand { left: 107px; top: 32px; }
  .copyright { position: absolute; right: 106px; top: 36px; font-size: 9.5px; color: #e6e6e6; }
</style>
</head>
<body>
  <header class="hero">
    <div class="hero-photo" role="img" aria-label="Photo of a crowd at a rally raising fists in solidarity"></div>
    <div class="site-header">
      <div class="brand"><span class="brand-dot"></span><span class="brand-name">Pelbo</span></div>
      <nav class="nav">
        <a href="#">Post Action</a>
        <a href="#">Your action</a>
        <a href="#">Register</a>
        <a href="#" class="login">Login</a>
      </nav>
    </div>
    <h1 class="hero-title">RACIAL JUSTICE</h1>
    <p class="hero-text">Lorem Ipsum is simply dummy text of the printing and types etting industry lorem Ipsum has been the industry.</p>
    <a href="#" class="store-btn">Quill web store</a>
  </header>

  <section class="steps">
    <svg width="970" height="427" viewBox="0 0 970 427" aria-hidden="true">
      <defs>
        <filter id="soft-shadow" x="-30%" y="-30%" width="160%" height="170%">
          <feDropShadow dx="0" dy="12" stdDeviation="10" flood-color="#8a97a8" flood-opacity=".18"/>
        </filter>
        <marker id="arrow-head" viewBox="0 0 10 10" refX="6" refY="5" markerWidth="5" markerHeight="5" orient="auto">
          <path d="M0 0 L10 5 L0 10 Z" fill="currentColor"/>
        </marker>
      </defs>
      <line x1="466" y1="73" x2="504" y2="73" stroke="var(--rule)" stroke-width="2"/>

      <circle cx="226" cy="238" r="120" fill="#fff" filter="url(#soft-shadow)"/>
      <circle cx="485" cy="238" r="120" fill="#fff" filter="url(#soft-shadow)"/>
      <circle cx="747" cy="238" r="120" fill="#fff" filter="url(#soft-shadow)"/>
      <circle cx="226" cy="238" r="108" fill="none" stroke="var(--orange)" stroke-width="5"/>
      <circle cx="485" cy="238" r="108" fill="none" stroke="var(--orange-mid)" stroke-width="5"/>
      <circle cx="747" cy="238" r="108" fill="none" stroke="var(--orange-soft)" stroke-width="5"/>

      <path d="M126 141 Q224 60 320 136" fill="none" stroke="var(--orange)" stroke-width="2.5" marker-end="url(#arrow-head)" style="color:var(--orange)"/>
      <path d="M645 141 Q743 60 840 136" fill="none" stroke="var(--orange)" stroke-width="2.5" marker-end="url(#arrow-head)" style="color:var(--orange)"/>
      <path d="M386 337 Q485 420 580 340" fill="none" stroke="var(--orange-mid)" stroke-width="2.5" marker-end="url(#arrow-head)" style="color:var(--orange-mid)"/>

      <g stroke="#111" stroke-width="1.6" fill="#fff">
        <line x1="341" y1="235" x2="368" y2="235"/>
        <circle cx="334" cy="235" r="7"/><circle cx="375" cy="235" r="7"/>
        <line x1="602" y1="235" x2="630" y2="235"/>
        <circle cx="595" cy="235" r="7"/><circle cx="637" cy="235" r="7"/>
      </g>

      <g fill="none" stroke="var(--orange)" stroke-width="1.6" stroke-linecap="round" stroke-linejoin="round">
        <circle cx="220" cy="183" r="13"/>
        <circle cx="220" cy="183" r="5"/>
        <path d="M238 196 L252 172 L256 175 L242 199 L236 201 Z"/>
        <path d="M472 163 h22 v34 h-22 z"/>
        <path d="M477 171 h12 M477 178 h12 M477 185 h12"/>
        <path d="M494 182 h8 v13 a4 4 0 0 1 -8 0"/>
        <circle cx="747" cy="183" r="20"/>
      </g>
    </svg>
    <h2 class="section-title">HOW THE QUILL EXTENSION WORKS</h2>
    <div class="step" style="left:146px">
      <h3>LOREM IPSUM</h3>
      <p>There are many variations of passages of Lorem Ipsum available, but the majority have suffered alteration in some form, by injected humour, or randomised</p>
    </div>
    <div class="step" style="left:405px">
      <h3>LOREM IPSUM</h3>
      <p>There are many variations of passages of Lorem Ipsum available, but the majority have suffered alteration in some form, by injected humour, or randomised</p>
    </div>
    <div class="step" style="left:668px">
      <h3>LOREM IPSUM</h3>
      <p>There are many variations of passages of Lorem Ipsum available, but the majority have suffered alteration in some form, by injected humour, or randomised</p>
    </div>
  </section>

  <section class="overview">
    <div class="overview-art" role="img" aria-label="Illustration of people connected in a circle"></div>
    <div class="overview-divider"></div>
    <h2 class="section-title">OVERVIEW</h2>
    <div class="overview-rule"></div>
    <div class="overview-body">
      <p>Facilitating social responsibility by connecting like minded individuals and to ways they may impact the real world</p>
      <p>Many of us read about social and political issues we care about every day, but may not know how to take concrete action to combat injustice and create meaningful change. Pelbo is a Quill extension that analyzes articles you are reading and recommends relevant actions you can take. By connecting you to organizers and movements, Pelbo can help you find ways to take part in building a more just, equitable, and sustainable future.</p>
    </div>
  </section>

  <footer class="site-footer">
    <div class="brand"><span class="brand-dot"></span><span class="brand-name">Pelbo</span></div>
    <p class="copyright">Copyright © 2022 All Rights Reserved</p>
  </footer>
</body>
</html>
```